Amber Reed Consulting Business Card

Hi Morwen. Thank you for your work on my coaching business card. I have another business which needs a new card. It is my counselling business. The best way to find out how to approach this project will be to go to my other website. www.amberreedconsulting.example.au and you will be able to see the colours scheme that I will require. White, Green and blue.

The tag line is Amber Reed Consulting So Walk toward a brighter day ahead. The clients are varied but mostly middle class Australian. The card is to show on it the same details as my other business card but with a different phone number. The tag lines are obviously different. The phone number is 5863 1427 The addresses are all the same.

Again simple, professional sophisticated is best.

Industry/Entity Type

Business

```html
<!DOCTYPE html>
<html lang="en">
<head>
<meta charset="utf-8">
<title>Amber Reed Consulting – Business Card</title>
<link href="https://fonts.googleapis.com/css2?family=Marcellus&family=Raleway:wght@300;400;500&display=swap" rel="stylesheet">
<style>
  :root {
    --backdrop: #e9e7e3;
    --card-blue-light: #4d78c4;
    --card-blue: #2a57a8;
    --card-blue-deep: #1c3f86;
    --white: #ffffff;
    --silver: #e4e9f2;
    --green: #a6cf3f;
    --sage: #a9c58a;
    --serif: 'Marcellus', Georgia, serif;
    --sans: 'Raleway', Arial, sans-serif;
  }
  * { box-sizing: border-box; margin: 0; padding: 0; }
  html, body { width: 1200px; height: 803px; overflow: hidden; }
  body {
    background: var(--backdrop);
    display: flex;
    align-items: center;
    justify-content: center;
    gap: 50px;
  }
  .card {
    position: relative;
    width: 540px;
    height: 330px;
    background: linear-gradient(160deg, var(--card-blue-light) 0%, var(--card-blue) 45%, var(--card-blue-deep) 100%);
    box-shadow: 0 6px 20px rgba(0,0,0,.25);
    color: var(--white);
    overflow: hidden;
  }
  /* Front */
  .card-front { padding: 0 40px; display: flex; flex-direction: column; justify-content: center; }
  .front-name {
    font-family: var(--serif);
    font-weight: 400;
    font-size: 38px;
    color: var(--silver);
    letter-spacing: 1px;
    line-height: 1;
    white-space: nowrap;
  }
  .front-rule { height: 2px; background: var(--green); margin: 10px 0 10px; width: 100%; }
  .front-tagline {
    font-family: var(--sans); font-weight: 300;
    font-size: 15.5px; letter-spacing: 2.6px; text-transform: uppercase;
    white-space: nowrap;
  }
  .front-services {
    margin-top: 8px;
    font-family: var(--sans); font-weight: 400;
    font-size: 12px; letter-spacing: 1.6px; text-transform: uppercase;
    color: var(--green); line-height: 1.45;
  }
  /* Back */
  .card-back { padding: 0 34px; display: flex; flex-direction: column; justify-content: center; }
  .holder { display: flex; align-items: baseline; gap: 8px; white-space: nowrap; }
  .holder-name { font-family: var(--sans); font-weight: 400; font-size: 19px; letter-spacing: 1px; text-transform: uppercase; }
  .holder-title { font-family: var(--sans); font-weight: 400; font-size: 11.5px; }
  .back-name {
    margin-top: 10px;
    font-family: var(--serif); font-weight: 400; font-size: 38px; color: var(--sage); line-height: 1;
    white-space: nowrap;
  }
  .back-tagline {
    margin-top: 6px;
    font-family: var(--sans); font-weight: 300; font-size: 14px;
    letter-spacing: 2.4px; text-transform: uppercase; color: var(--sage);
    white-space: nowrap;
  }
  .back-rule { height: 1px; background: var(--white); margin: 14px 0 14px; }
  .contact-grid { display: grid; grid-template-columns: 1fr 1.35fr; row-gap: 5px; font-family: var(--sans); font-size: 11.5px; }
  .contact-item { display: flex; align-items: center; gap: 7px; color: var(--sage); white-space: nowrap; }
  .contact-item svg { width: 12px; height: 12px; flex: none; }
  .offices { margin-top: 10px; font-family: var(--sans); font-size: 11px; color: var(--green); line-height: 1.55; white-space: nowrap; }
</style>
</head>
<body>
  <section class="card card-front" aria-label="Card front">
    <h1 class="front-name">Amber Reed Consulting</h1>
    <div class="front-rule"></div>
    <p class="front-tagline">Walk toward a brighter day ahead</p>
    <p class="front-services">Advanced counselling • Coaching • Hypnotherapy<br>and psychotherapy</p>
  </section>

  <section class="card card-back" aria-label="Card back">
    <div class="holder">
      <span class="holder-name">Morwen Hale</span>
      <span class="holder-title">Clinical Psychotherapist and Executive Coach</span>
    </div>
    <h2 class="back-name">Amber Reed Consulting</h2>
    <p class="back-tagline">Walk toward a brighter day ahead</p>
    <div class="back-rule"></div>
    <div class="contact-grid">
      <div class="contact-item">
        <svg viewBox="0 0 12 12" aria-hidden="true"><path d="M2 4c0-1.5 8-1.5 8 0v1H8V4H4v1H2z M3 6h6l1 4H2z" fill="#fff"/></svg>
        <span>+612 5863 1427</span>
      </div>
      <div class="contact-item">
        <svg viewBox="0 0 12 12" aria-hidden="true"><rect x="1" y="2.5" width="10" height="7" fill="#fff"/><path d="M1 2.5l5 4 5-4" stroke="#2a57a8" fill="none"/></svg>
        <span>morwen@morwenhale.example.au</span>
      </div>
      <div class="contact-item">
        <svg viewBox="0 0 12 12" aria-hidden="true"><rect x="2" y="1.5" width="8" height="4" fill="#fff"/><rect x="1" y="5.5" width="10" height="5" fill="#fff"/></svg>
        <span>+612 5863 1429</span>
      </div>
      <div class="contact-item">
        <svg viewBox="0 0 12 12" aria-hidden="true"><circle cx="6" cy="6" r="5" fill="#fff"/></svg>
        <span>www.amberreedconsulting.example.au</span>
      </div>
    </div>
    <p class="offices">
      Rozelle Office: 48 Wattle Lane Rozelle NSW 2039<br>
      Northbridge Office: Suite 210 / 17 Fernhill Street Northbridge NSW 2063<br>
      Kentwell Street Office: Suite 508 / 92 Kentwell Street Sydney CBD NSW 2000
    </p>
  </section>
</body>
</html>
```